Business Card Design

We are a family run drainage & groundworks company that specialise in treatment plant installation. We work for commercial & domestic property's, we have specialised knowledge & equipment for CCTV surveys, jetting blockages & repairing all types of drainage systems.

Industry/Entity Type

Business

Contact Information for Business Card

14 Millbrook Works
Tallowen Park Lane
Harnwick
Kelmshire
SP9 4DW
Tel: 01632 960418
Fax: 01632 960773
Mobile: 07700 900382
enquiries@larkes.co.uk
www.larkfieldenvironmentalservices.co.uk

Requirements
Must have
• logo, address, the right colour green.
I need the cards to also have individuals names:

Tom marlowe
Dan Whitcombe
Emma Marlowe
Kay Dunmore

And also some with just the name & address on :)

```html
<!DOCTYPE html>
<html lang="en">
<head>
<meta charset="utf-8">
<title>Larkfield Environmental Services – Business Card</title>
<link href="https://fonts.googleapis.com/css2?family=Open+Sans:wght@400;700;800&display=swap" rel="stylesheet">
<style>
  :root {
    --brand-green: #009640;
    --card-white: #ffffff;
    --backdrop: #eeeeee;
    --shadow: rgba(0, 0, 0, 0.18);
  }

  * { box-sizing: border-box; margin: 0; padding: 0; }

  html, body {
    width: 1200px;
    height: 1200px;
    overflow: hidden;
  }

  body {
    background: var(--backdrop);
    font-family: "Open Sans", Arial, sans-serif;
    position: relative;
  }

  .card {
    position: absolute;
    width: 720px;
    height: 400px;
    box-shadow: 0 6px 18px var(--shadow);
    overflow: hidden;
  }

  /* Front of card */
  .card--front {
    left: 150px;
    top: 170px;
    display: flex;
    background: var(--card-white);
  }

  .brand-panel {
    width: 270px;
    height: 100%;
    background: var(--card-white);
    display: flex;
    align-items: center;
    justify-content: center;
    padding: 0 20px;
  }

  .brand-lockup {
    display: flex;
    align-items: center;
    gap: 12px;
  }

  .brand-lockup__mark {
    width: 40px;
    height: 40px;
    background: var(--brand-green);
    flex-shrink: 0;
  }

  .brand-lockup__name {
    color: var(--brand-green);
    font-weight: 700;
    font-size: 21px;
    line-height: 1.15;
  }

  .contact-panel {
    flex: 1;
    height: 100%;
    background: var(--brand-green);
    position: relative;
    color: var(--card-white);
    text-align: right;
  }

  .name-bar {
    position: absolute;
    top: 58px;
    left: 60px;
    right: 0;
    height: 58px;
    background: var(--card-white);
    display: flex;
    align-items: center;
    justify-content: flex-end;
    padding-right: 26px;
  }

  .name-bar__name {
    color: var(--brand-green);
    font-weight: 700;
    font-size: 34px;
    letter-spacing: 0.2px;
  }

  .contact-details {
    position: absolute;
    top: 134px;
    right: 26px;
    font-size: 18px;
    line-height: 24px;
  }

  .contact-details__address {
    font-weight: 700;
    font-style: normal;
  }

  .contact-details__line {
    font-weight: 400;
  }

  .contact-details__line--email {
    margin-top: 4px;
  }

  .website {
    font-weight: 700;
    font-size: 19px;
    color: var(--card-white);
    white-space: nowrap;
  }

  .contact-panel .website {
    position: absolute;
    right: 26px;
    bottom: 26px;
  }

  /* Back of card */
  .card--back {
    left: 330px;
    top: 630px;
    background: var(--brand-green);
    display: flex;
    align-items: center;
    justify-content: center;
  }

  .card--back .website {
    font-size: 20px;
  }
</style>
</head>
<body>

  <section class="card card--front" aria-label="Business card front">
    <div class="brand-panel">
      <div class="brand-lockup">
        <span class="brand-lockup__mark"></span>
        <span class="brand-lockup__name">Larkfield<br>Environmental<br>Services</span>
      </div>
    </div>

    <div class="contact-panel">
      <div class="name-bar">
        <span class="name-bar__name">Tom marlowe</span>
      </div>

      <div class="contact-details">
        <address class="contact-details__address">
          14 Millbrook Works<br>
          Tallowen Park Lane<br>
          Harnwick<br>
          Kelmshire SP9 4DW
        </address>
        <p class="contact-details__line">T : 01632 960418</p>
        <p class="contact-details__line">F : 01632 960773</p>
        <p class="contact-details__line">M : 07700 900382</p>
        <p class="contact-details__line contact-details__line--email">E : enquiries@larkes.co.uk</p>
      </div>

      <p class="website">www.larkfieldenvironmentalservices.co.uk</p>
    </div>
  </section>

  <section class="card card--back" aria-label="Business card back">
    <p class="website">www.larkfieldenvironmentalservices.co.uk</p>
  </section>

</body>
</html>
```